Flyer für Kinderschminken, Schwangerschaftsbemalung, Glitzertattoos
Alles bestens war eine tolle Zusammenarbeit würde mich jederzeit wieder an sie wenden. Bin sehr glücklich mich für den Designer 7qv entschieden zu haben.
Zielgruppe
Ich biete Kinderschminken, Glitzer-Tattoos, Wundenschminken und Schwangerschaftsbemalung an so wie Vermietung von einer Popkornmaschine.
Aufgabenstellung
Schön wäre es, wenn Sie sich an meiner Internetseite orientieren.
Wichtig ist das Logo und eine Übersicht meiner Leistung.
Gern würde ich über den Flyer vermitteln, was mich abhebt beziehungsweise vorauf ich acht lege und was eine professionelle Kinderschminktante aus macht.
Ich achte auf Hygiene, bilde mich immer wieder weiter, besuche Fortbildungen und habe hochwertige Produkte / Farben, die eine EU-Kosmetik Verordnung haben und somit hautverträglich sind.
Ich habe an einen A6 Flyer gedacht beidseitig bin aber offen für neue Ideen und Vorschläge.
https://frau-sonnentau.de

```html
<!DOCTYPE html>
<html lang="de">
<head>
<meta charset="utf-8">
<title>Frau Sonnentau – Flyer Kinderschminken</title>
<link rel="stylesheet" href="https://fonts.googleapis.com/css2?family=Amatic+SC:wght@400;700&family=Poppins:wght@400;500;600&display=swap">
<style>
  :root {
    --stage: #c4b6c9;
    --sky: #e2f0f8;
    --white: #ffffff;
    --purple: #a24f9b;
    --teal: #1d9fae;
    --ink: #5f5a55;
    --ink-strong: #4a4541;
  }
  * { box-sizing: border-box; margin: 0; padding: 0; }
  html, body { width: 1200px; height: 848px; overflow: hidden; }
  body { background: var(--stage); font-family: "Poppins", sans-serif; position: relative; }

  .flyer { position: absolute; top: 105px; width: 425px; height: 598px; background: var(--sky); overflow: hidden; }
  .flyer--front { left: 161px; }
  .flyer--back { left: 644px; }

  /* front */
  .photo { position: absolute; top: 0; height: 212px; border-radius: 0 0 60px 60px / 0 0 30px 30px; }
  .photo--bird { left: 0; width: 123px; background: linear-gradient(160deg, #cf9e86, #b98570 60%, #7d8a6e); }
  .photo--belly { left: 134px; width: 159px; height: 222px; background: radial-gradient(ellipse at 50% 45%, #d9d9d6 0 30%, #8b8682 55%, #3e3530 85%); }
  .photo--tiger { left: 304px; width: 121px; height: 212px; background: linear-gradient(170deg, #e6b7a4, #d9a18c); }

  .headline { position: absolute; left: 0; width: 425px; text-align: center; font-family: "Amatic SC", cursive; font-weight: 400; color: var(--purple); line-height: 1; text-transform: uppercase; white-space: nowrap; }
  .headline--main { top: 232px; font-size: 64px; }
  .headline--sub { top: 294px; font-size: 64px; left: 8px; }

  .services { position: absolute; top: 376px; left: 0; width: 425px; display: flex; justify-content: center; align-items: center; gap: 6px; font-family: "Amatic SC", cursive; font-size: 19px; color: var(--purple); white-space: nowrap; text-transform: uppercase; }
  .services .heart { width: 12px; height: 11px; }

  .bottom-cloud { position: absolute; left: 0; top: 430px; width: 425px; height: 168px; }
  .brand { position: absolute; left: 40px; top: 476px; display: flex; align-items: center; gap: 8px; }
  .brand__dot { width: 12px; height: 12px; border-radius: 50%; background: var(--teal); }
  .brand__name { font-family: "Poppins", sans-serif; font-weight: 500; font-size: 24px; color: var(--teal); letter-spacing: 0.5px; }
  .brand__tag { position: absolute; left: 40px; top: 512px; font-size: 7px; color: var(--ink); letter-spacing: 0.6px; text-transform: uppercase; }
  .mascot { position: absolute; left: 280px; top: 410px; width: 70px; height: 126px; border-radius: 34px 34px 10px 10px; background: linear-gradient(180deg, #f1ece6, #d7e9ec 55%, #f4d6de); }

  .contact { position: absolute; left: 16px; width: 393px; font-size: 11px; font-weight: 500; color: var(--teal); display: flex; justify-content: space-between; align-items: center; }
  .contact--row1 { top: 557px; }
  .contact--row2 { top: 573px; }
  .contact span { display: inline-flex; align-items: center; gap: 6px; }
  .contact svg { width: 12px; height: 12px; }

  /* back */
  .back-top { position: absolute; left: 0; top: 0; width: 425px; height: 150px; }
  .feature { position: absolute; display: flex; align-items: center; gap: 8px; color: var(--purple); font-size: 13.2px; font-weight: 500; line-height: 1.18; text-transform: uppercase; }
  .feature svg { width: 24px; height: 24px; flex: none; }
  .feature--training { left: 213px; top: 22px; }
  .feature--products { left: 135px; top: 66px; }
  .feature--hygiene { left: 38px; top: 104px; }
  .divider { position: absolute; left: 21px; top: 152px; width: 385px; height: 3px; background: var(--purple); border-radius: 2px; }

  .offer-photo { position: absolute; width: 86px; height: 86px; border-radius: 50%; }
  .offer-photo--kids { left: 36px; top: 160px; background: radial-gradient(circle at 55% 45%, #e8b9a5, #c95a4a 45%, #5b6a4c); }
  .offer-photo--wound { left: 304px; top: 243px; background: radial-gradient(circle at 40% 40%, #a83a44, #e1b29e 55%, #8a5a3e); }
  .offer-photo--belly { left: 33px; top: 326px; background: radial-gradient(circle at 50% 45%, #dcdcd8, #8a847e 50%, #3a302b 85%); }
  .offer-photo--glitter { left: 306px; top: 411px; background: radial-gradient(circle at 50% 45%, #c486b6, #e5b6a6 50%, #c9978a); }
  .offer-photo--popcorn { left: 34px; top: 498px; background: radial-gradient(circle at 50% 55%, #e4c98a 0 18%, #d6373a 19% 34%, #1d9fae 36%); }

  .offer-text { position: absolute; font-size: 11.6px; line-height: 15.6px; color: var(--ink); text-transform: uppercase; }
  .offer-text b { font-weight: 600; color: var(--ink-strong); }
  .offer-text--left { left: 136px; }
  .offer-text--right { right: 130px; text-align: right; }
  .offer-text--kids { top: 177px; }
  .offer-text--wound { top: 249px; }
  .offer-text--belly { top: 360px; left: 141px; }
  .offer-text--glitter { top: 420px; }
  .offer-text--popcorn { top: 507px; left: 141px; }
</style>
</head>
<body>

<section class="flyer flyer--front" aria-label="Flyer Vorderseite">
  <div class="photo photo--bird" role="img" aria-label="Foto: blaues Glitzertattoo eines Adlers auf einem Oberarm"></div>
  <div class="photo photo--belly" role="img" aria-label="Foto: Belly Paint mit Baby-Motiv auf einem Schwangerschaftsbauch"></div>
  <div class="photo photo--tiger" role="img" aria-label="Foto: schwarzes Tattoo eines Tigerbabys auf der Haut"></div>

  <h1 class="headline headline--main">Kinderschminken</h1>
  <div class="headline headline--sub">&amp; Mehr</div>

  <div class="services">
    <span>Glitzertattoos</span>
    <svg class="heart" viewBox="0 0 24 22"><path fill="var(--teal)" d="M12 21 C4 14 0 10 0 6 A6 6 0 0 1 12 3 A6 6 0 0 1 24 6 C24 10 20 14 12 21Z"/></svg>
    <span>Kinderschminken</span>
    <svg class="heart" viewBox="0 0 24 22"><path fill="var(--teal)" d="M12 21 C4 14 0 10 0 6 A6 6 0 0 1 12 3 A6 6 0 0 1 24 6 C24 10 20 14 12 21Z"/></svg>
    <span>Belly Paint</span>
    <svg class="heart" viewBox="0 0 24 22"><path fill="var(--teal)" d="M12 21 C4 14 0 10 0 6 A6 6 0 0 1 12 3 A6 6 0 0 1 24 6 C24 10 20 14 12 21Z"/></svg>
    <span>Grusel-Looks</span>
  </div>

  <svg class="bottom-cloud" viewBox="0 0 425 168" preserveAspectRatio="none" aria-hidden="true">
    <path fill="var(--white)" d="M0 168 V22 Q30 -2 62 14 Q95 -6 128 28 Q175 10 210 30 Q250 0 300 24 Q345 -4 380 16 Q405 6 425 18 V168 Z"/>
  </svg>

  <div class="mascot" role="img" aria-label="Illustration: Mädchen mit Pinsel als Maskottchen"></div>
  <div class="brand">
    <span class="brand__dot"></span>
    <span class="brand__name">Frau Sonnentau</span>
  </div>
  <div class="brand__tag">Kinderschminken &amp; Glitzer Tattoos</div>

  <div class="contact contact--row1">
    <span>
      <svg viewBox="0 0 24 24"><rect x="2" y="5" width="20" height="14" fill="none" stroke="var(--teal)" stroke-width="2"/><path d="M2 5 L12 13 L22 5" fill="none" stroke="var(--teal)" stroke-width="2"/></svg>
      KinderschminkenSonnentau@post.de
    </span>
    <span>
      0160 / 55 12 904
      <svg viewBox="0 0 24 24"><path fill="var(--teal)" d="M6 2 L10 7 L8 10 Q10 14 14 16 L17 14 L22 18 L19 22 Q4 20 2 5 Z"/></svg>
    </span>
  </div>
  <div class="contact contact--row2">
    <span>
      <svg viewBox="0 0 24 24"><circle cx="12" cy="12" r="10" fill="var(--teal)"/><path d="M2 12 H22 M12 2 Q6 12 12 22 M12 2 Q18 12 12 22" fill="none" stroke="#fff" stroke-width="1.5"/></svg>
      www.frau-sonnentau.de
    </span>
    <span>
      01234 Birkenau OT Wiesental
      <svg viewBox="0 0 24 24"><path d="M12 22 C6 14 4 11 4 8 A8 8 0 0 1 20 8 C20 11 18 14 12 22Z" fill="none" stroke="var(--teal)" stroke-width="2"/><circle cx="12" cy="8" r="3" fill="none" stroke="var(--teal)" stroke-width="2"/></svg>
    </span>
  </div>
</section>

<section class="flyer flyer--back" aria-label="Flyer Rückseite">
  <svg class="back-top" viewBox="0 0 425 150" preserveAspectRatio="none" aria-hidden="true">
    <path fill="var(--white)" d="M0 0 H425 V100 Q400 82 370 96 Q340 70 300 92 Q260 80 230 100 Q190 68 150 92 Q110 78 80 96 Q45 80 20 100 Q8 94 0 98 Z"/>
  </svg>

  <div class="feature feature--training">
    <svg viewBox="0 0 24 24"><rect x="7" y="2" width="14" height="17" fill="none" stroke="var(--teal)" stroke-width="2"/><rect x="3" y="6" width="12" height="16" fill="var(--white)" stroke="var(--teal)" stroke-width="2"/></svg>
    <span>Stetige Teilnahme an<br>Fortbildungen</span>
  </div>
  <div class="feature feature--products">
    <svg viewBox="0 0 24 24"><circle cx="12" cy="13" r="8" fill="none" stroke="var(--teal)" stroke-width="2"/><path d="M8 13 L11 16 L16 10" fill="none" stroke="var(--teal)" stroke-width="2"/><circle cx="12" cy="2" r="1.3" fill="var(--teal)"/><circle cx="5" cy="4" r="1.3" fill="var(--teal)"/><circle cx="19" cy="4" r="1.3" fill="var(--teal)"/></svg>
    <span>Hochwertige<br>Produkte</span>
  </div>
  <div class="feature feature--hygiene">
    <svg viewBox="0 0 24 24"><circle cx="5" cy="4" r="2.5" fill="none" stroke="var(--teal)" stroke-width="1.8"/><circle cx="11" cy="3" r="2" fill="none" stroke="var(--teal)" stroke-width="1.8"/><path d="M2 14 H14 Q18 14 18 18 H8 M2 14 V22 H20 Q23 22 22 18" fill="none" stroke="var(--teal)" stroke-width="2"/></svg>
    <span>Hoher<br>Hygieneanspruch</span>
  </div>
  <div class="divider"></div>

  <div class="offer-photo offer-photo--kids" role="img" aria-label="Foto: Kind beim Kinderschminken"></div>
  <p class="offer-text offer-text--left offer-text--kids">Verzaubern Sie die kleinen Gäste<br>auf Ihrem Event mit unserem<br><b>Kinderschminken</b>!</p>

  <p class="offer-text offer-text--right offer-text--wound">Erwecken Sie fesselnde<br>Geschichten zum Leben und<br>verblüffen Sie Ihre Freunde<br>mit professionellem<br><b>Wunden-Schminken</b>!</p>
  <div class="offer-photo offer-photo--wound" role="img" aria-label="Foto: Wunden-Schminken im Gesicht"></div>

  <div class="offer-photo offer-photo--belly" role="img" aria-label="Foto: Belly Paint auf einem Schwangerschaftsbauch"></div>
  <p class="offer-text offer-text--belly">Entdecken Sie die zauberhafte<br>Welt der <b>Belly Paints</b>!</p>

  <p class="offer-text offer-text--right offer-text--glitter">Entdecken Sie die Magie der<br><b>Glitzer-Tattoos</b>, die wasserfest<br>sind und je nach Pflege bis zu 2<br>Wochen lang halten!</p>
  <div class="offer-photo offer-photo--glitter" role="img" aria-label="Foto: Glitzer-Tattoo auf der Haut"></div>

  <div class="offer-photo offer-photo--popcorn" role="img" aria-label="Illustration: Popcorn-Tüte auf türkisem Kreis"></div>
  <p class="offer-text offer-text--popcorn">Popcorn-Vergnügen auf Ihrer<br>Veranstaltung! Mit unseren<br><b>Popcorn-Maschinen</b> wird Ihre<br>Feier zum vollen Erfolg.</p>
</section>

</body>
</html>
```